Water Management Company Letterhead

Looking for a eye-catching design of letterhead for a California based parent company of water management products. The letterhead would need to include the three logos of the sub-companies, with "The Brookline Collective LLC" (parent company) being the primary focus. Please include the sub-company logos in the following order of significance: Velmoro, Drifting Reeds North, and then Gromtile NE. The color schemes should convey water/enviornment - blues and greens. Most importantly it should be something that will stand out. All logos are uploaded. Thank you for your interest!

Target Market(s)

Environmental conservationists, government agencies, etc.

Industry/Entity Type

Environment

Font styles to use
Serif
Sans Serif

Colors
33a6d7
3276b5
abd037
cadf82
85cae6
85acd3

Requirements
Must have
• eye-catching, blue and green tones pulled from logos, water droplet.

```html
<!DOCTYPE html>
<html lang="en">
<head>
<meta charset="utf-8">
<title>The Brookline Collective LLC — Letterhead</title>
<link rel="stylesheet" href="https://fonts.googleapis.com/css2?family=Cinzel:wght@400;500&family=Open+Sans:wght@400;700&display=swap">
<style>
  :root {
    --backdrop: #e9eaec;
    --paper: #ffffff;
    --ink: #1d1d1f;
    --brand-navy: #2a3760;
    --water-blue: #33a6d7;
    --deep-blue: #3276b5;
    --leaf-green: #abd037;
    --soft-green: #cadf82;
    --sky: #85cae6;
    --contact-grey: #4a4a4a;
    --signature-tone: #d9dadd;
    --partner-brown: #8a5a3c;
  }
  * { box-sizing: border-box; margin: 0; padding: 0; }
  html, body { width: 1200px; height: 1000px; overflow: hidden; }
  body {
    background: var(--backdrop);
    font-family: "Open Sans", Arial, sans-serif;
    color: var(--ink);
    position: relative;
  }
  .letterhead {
    position: absolute;
    left: 240px;
    top: 34px;
    width: 720px;
    height: 932px;
    background: var(--paper);
    box-shadow: 0 6px 24px rgba(0,0,0,0.12);
  }
  .contact-block {
    position: absolute;
    top: 52px;
    right: 70px;
    font-size: 9.5px;
    line-height: 13px;
    color: var(--contact-grey);
  }
  .contact-row { display: flex; align-items: center; gap: 6px; }
  .contact-icon { width: 11px; height: 11px; flex: none; }
  .contact-address { padding-left: 17px; }
  .brand-mark {
    position: absolute;
    top: 150px;
    left: 70px;
    display: flex;
    align-items: center;
    gap: 10px;
  }
  .brand-dot {
    width: 20px; height: 20px; border-radius: 50%;
    background: var(--water-blue);
  }
  .brand-name {
    font-family: "Cinzel", Georgia, serif;
    font-weight: 500;
    font-size: 34px;
    letter-spacing: 0.5px;
    color: var(--brand-navy);
  }
  .recipient {
    position: absolute;
    top: 250px;
    left: 70px;
    font-size: 12px;
    font-weight: 700;
    line-height: 19px;
  }
  .letter-body {
    position: absolute;
    top: 345px;
    left: 70px;
    width: 580px;
    font-size: 12px;
    line-height: 20px;
  }
  .letter-body p { margin-bottom: 22px; }
  .sign-off {
    position: absolute;
    top: 655px;
    left: 70px;
    font-size: 12px;
  }
  .signature {
    width: 150px; height: 56px; margin: 8px 0 6px;
    background: var(--signature-tone);
    border-radius: 4px;
  }
  .partner-row {
    position: absolute;
    left: 70px;
    right: 70px;
    bottom: 70px;
    display: flex;
    justify-content: space-between;
    align-items: center;
  }
  .partner {
    display: flex; align-items: center; gap: 7px;
    font-size: 15px; font-weight: 400;
  }
  .partner-velmoro { color: var(--deep-blue); }
  .partner-velmoro .partner-shape { background: var(--water-blue); border-radius: 50%; }
  .partner-reeds { color: var(--water-blue); }
  .partner-reeds .partner-shape { background: var(--leaf-green); border-radius: 50%; }
  .partner-gromtile { color: var(--partner-brown); }
  .partner-gromtile .partner-shape { background: var(--partner-brown); }
  .partner-shape { width: 14px; height: 14px; }
  .page-edge {
    position: absolute; left: 0; right: 0; bottom: 0; height: 4px;
    background: linear-gradient(90deg, var(--sky), var(--soft-green));
  }
</style>
</head>
<body>
  <main class="letterhead">
    <div class="contact-block">
      <div class="contact-row">
        <svg class="contact-icon" viewBox="0 0 12 12"><rect width="12" height="12" rx="2" fill="#3276b5"/><path d="M3.5 2.8c.5 2.8 2.6 5.2 5.6 5.9l.7-1.4-1.5-.8-.7.8C6.5 6.8 5.4 5.6 5 4.5l.8-.6L5 2.2z" fill="#fff"/></svg>
        <span>(000) 555-0142</span>
      </div>
      <div class="contact-row">
        <svg class="contact-icon" viewBox="0 0 12 12"><rect width="12" height="12" rx="2" fill="#3276b5"/><rect x="2.5" y="3.5" width="7" height="5" fill="none" stroke="#fff"/><path d="M2.5 3.5l3.5 3 3.5-3" fill="none" stroke="#fff"/></svg>
        <span>hello@brooklinecollective.com</span>
      </div>
      <div class="contact-row">
        <svg class="contact-icon" viewBox="0 0 12 12"><rect width="12" height="12" rx="2" fill="#3276b5"/><circle cx="6" cy="6" r="3.3" fill="none" stroke="#fff"/><path d="M2.7 6h6.6M6 2.7v6.6" stroke="#fff" stroke-width=".8"/></svg>
        <span>www.brooklinecollective.com</span>
      </div>
      <div class="contact-address">Address Line 1<br>Area Name Lindale, CA 90410</div>
    </div>

    <div class="brand-mark">
      <span class="brand-dot"></span>
      <span class="brand-name">The Brookline Collective LLC</span>
    </div>

    <div class="recipient">
      To<br>Lorem Ipsum is simply<br>Lorem Ipsum is Lorem Ipsum is<br>Lorem Ipsum is
    </div>

    <div class="letter-body">
      <p>dummy text of the printing and typesetting industry. Lorem Ipsum has been the industry's standard dummy text ever since the 1500s, when an unknown printer took a galley of type and scrambled it to make a type specimen book. It has survived not only five centuries, but also the leap into electronic typesetting, remaining essentially unchanged.</p>
      <p>It is a long established fact that a reader will be distracted by the readable content of a page when looking at its layout. The point of using Lorem Ipsum is that it has a more-or-less normal distribution of letters, as opposed to using 'Content here, content here', making it look like readable English. Many desktop publishing packages and web page editors now use Lorem Ipsum as their default model text, and a search for 'lorem'.</p>
      <p>Contrary to popular belief, Lorem Ipsum is not simply random text. It has roots in a piece of classical Latin literature from 45 BC, making it over 2000 years old. A Latin professor at a college in Virginia looked up one of the more obscure Latin words, consectetur, from a Lorem Ipsum passage.</p>
    </div>

    <div class="sign-off">
      Lorem Ipsum
      <div class="signature" role="img" aria-label="Handwritten signature"></div>
      Lorem Ipsum is a dummy
    </div>

    <footer class="partner-row">
      <div class="partner partner-velmoro"><span class="partner-shape"></span>Velmoro</div>
      <div class="partner partner-reeds"><span class="partner-shape"></span>Drifting Reeds North</div>
      <div class="partner partner-gromtile"><span class="partner-shape"></span>Gromtile NE</div>
    </footer>
    <div class="page-edge"></div>
  </main>
</body>
</html>
```